Business card for Luxury Portable Restroom Trailer company

We are a Luxury Portable Restroom Trailer Company Called FALCRIDGE HIRES. Based in Orange County California. We provide portable restroom trailers for events, such as, Weddings, Concerts, Charity events, Sporting events, Tournaments, Corporate events, ect. We rent and Sell the Luxury restrooms. Our colors are white, grey, and Orange. As you will see in the logo we uploaded.
There are 2 people in the company so the names and titles will change for the 3 people but card will remain the same. Here is the information for each Person: Dwight Penner CFO 555 318-0476
next Person: Leon Marchetti VP 555 318-0476
Next Person: Owen Marchetti CEO 555 318-0476
Information to include on the card: Luxury Restroom Trailers Rental and Sales. Weddings, Concerts, Charity, Sporting and Corp. Events.

```html
<!DOCTYPE html>
<html lang="en">
<head>
<meta charset="utf-8">
<title>Falcridge Hires – Business Card</title>
<link href="https://fonts.googleapis.com/css2?family=Arimo:wght@400;700&display=swap" rel="stylesheet">
<style>
  :root {
    --backdrop: #3a3a3a;
    --card: #2d2d2d;
    --orange: #f26f21;
    --grey-mark: #5a5a5a;
    --white: #ffffff;
    --soft-white: #e6e6e6;
  }
  * { margin: 0; padding: 0; box-sizing: border-box; }
  html, body {
    width: 1200px; height: 689px; overflow: hidden;
    background: var(--backdrop);
    font-family: "Arimo", Arial, sans-serif;
  }
  .canvas {
    position: relative; width: 1200px; height: 689px;
    display: flex; align-items: center; justify-content: center; gap: 48px;
  }
  .card {
    position: relative; width: 520px; height: 297px;
    background: var(--card);
    border-radius: 16px;
    border-bottom: 4px solid var(--orange);
    box-shadow: 0 18px 40px rgba(0,0,0,0.45);
    overflow: hidden;
  }
  /* back side */
  .card--back .brand {
    position: absolute; left: 0; right: 0; top: 86px;
    text-align: center;
  }
  .brand-name {
    display: inline-block;
    font-weight: 700; font-size: 38px; letter-spacing: 3px;
    color: var(--grey-mark);
  }
  .card--back .tagline {
    position: absolute; left: 0; right: 0; top: 178px;
    text-align: center; color: var(--white);
    font-size: 15px; line-height: 22px;
  }
  /* front side */
  .card--front .brand {
    position: absolute; left: 34px; top: 70px;
  }
  .card--front .brand-name {
    font-size: 30px; letter-spacing: 2px; color: var(--orange);
  }
  .person {
    position: absolute; left: 34px; top: 150px;
  }
  .person-name {
    font-weight: 700; font-size: 22px; color: var(--orange);
    text-transform: uppercase; letter-spacing: 0.5px;
  }
  .person-title {
    font-size: 14px; color: var(--white); margin-top: 4px;
  }
  .contacts {
    position: absolute; left: 34px; top: 214px;
    list-style: none; color: var(--soft-white); font-size: 14px;
  }
  .contacts li {
    display: flex; align-items: center; gap: 10px; height: 20px;
  }
  .contacts svg { width: 12px; height: 12px; fill: var(--orange); flex: none; }
</style>
</head>
<body>
<main class="canvas">
  <section class="card card--back" aria-label="Card back">
    <div class="brand"><span class="brand-name">FALCRIDGE HIRES</span></div>
    <p class="tagline">Luxury Restroom Trailers Rental and Sales.<br>Weddings • Concerts • Charity • Sporting and Corp. Events</p>
  </section>

  <section class="card card--front" aria-label="Card front">
    <div class="brand"><span class="brand-name">FALCRIDGE HIRES</span></div>
    <div class="person">
      <p class="person-name">Dwight Penner</p>
      <p class="person-title">CFO</p>
    </div>
    <ul class="contacts">
      <li>
        <svg viewBox="0 0 12 12" aria-hidden="true"><path d="M2.5 0.5 L4.5 0.5 L5.2 3 L3.8 4.2 C4.4 5.8 6 7.5 7.8 8.2 L9 6.8 L11.5 7.5 L11.5 9.5 C11.5 10.6 10.6 11.5 9.5 11.5 C4.8 11.2 0.8 7.2 0.5 2.5 C0.5 1.4 1.4 0.5 2.5 0.5 Z"/></svg>
        555 318-0476
      </li>
      <li>
        <svg viewBox="0 0 12 12" aria-hidden="true"><path d="M0.5 2 H11.5 V10 H0.5 Z M1.2 2.6 L6 6.4 L10.8 2.6" stroke="#2d2d2d" stroke-width="0.9"/></svg>
        info@falcridgehires.com
      </li>
      <li>
        <svg viewBox="0 0 12 12" aria-hidden="true"><circle cx="6" cy="6" r="5.5"/><path d="M0.5 6 H11.5 M6 0.5 C3.5 3.5 3.5 8.5 6 11.5 M6 0.5 C8.5 3.5 8.5 8.5 6 11.5" fill="none" stroke="#2d2d2d" stroke-width="0.8"/></svg>
        www.falcridgehires.com
      </li>
    </ul>
  </section>
</main>
</body>
</html>
```